Professional Photography Business cards

I need business cards that include my logo which I have uploaded. I run a photography business. I am open to ideas but I would like one side to have my logo and the other side to have my contact info. I don't have a website made but I do own a website domain. I have uploaded 2 different logo color schemes. My business colors are Blue, black , and white.

Business Name
Business Phone Number
Business Email
Business Website address
Instagram

Industry/Entity Type

Professional Photography

Contact Information for Business Card

Phone Number: 916-384-7702 email: info@tlane-studio.example Instagram: @t.lanestudio website doman- www.tlane-studio.example

Requirements
Must have
• I like the idea of a business card with a full black background front and back of card. My colors must include royal blue, black, and white

```html
<!DOCTYPE html>
<html lang="en">
<head>
<meta charset="utf-8">
<title>T. Lane Studio – Business Cards</title>
<link rel="stylesheet" href="https://fonts.googleapis.com/css2?family=Arimo:wght@400&display=swap">
<style>
  :root {
    --backdrop: #1c1c1c;
    --card-black: #000000;
    --card-white: #ffffff;
    --royal-blue: #0a17a6;
    --ink: #111111;
    --rule: #8a8a8a;
  }
  * { box-sizing: border-box; margin: 0; padding: 0; }
  html, body {
    width: 1200px; height: 1015px; overflow: hidden;
    background: var(--backdrop);
    font-family: "Arimo", Arial, sans-serif;
  }
  .sheet {
    width: 1200px; height: 1015px;
    display: flex; flex-direction: column; align-items: center; justify-content: center;
    gap: 40px;
  }
  .card {
    position: relative;
    width: 800px; height: 457px;
    overflow: hidden;
    box-shadow: 0 12px 30px rgba(0,0,0,.55);
  }
  .card--front { background: var(--card-black); }
  .card--back { background: var(--card-white); }

  .brand {
    display: flex; align-items: center; gap: 14px;
  }
  .brand__dot {
    width: 18px; height: 18px; border-radius: 50%;
    background: var(--royal-blue);
  }
  .brand__name {
    font-size: 46px; font-weight: 400; letter-spacing: 2px;
    color: var(--royal-blue); white-space: nowrap;
  }
  .card--front .brand {
    position: absolute; left: 50%; top: 50%;
    transform: translate(-50%, -50%);
  }
  .card--front .brand__dot { background: var(--card-white); }

  .card--back .brand {
    position: absolute; left: 60px; top: 190px;
  }
  .card--back .brand__name { font-size: 38px; }

  .divider {
    position: absolute; left: 440px; top: 120px;
    width: 1px; height: 180px; background: var(--rule);
  }
  .contacts {
    position: absolute; left: 468px; top: 128px;
    list-style: none;
    display: flex; flex-direction: column; gap: 16px;
  }
  .contacts__item {
    display: flex; align-items: center; gap: 12px;
    font-size: 19px; color: var(--ink);
  }
  .contacts__icon {
    width: 26px; height: 26px; border-radius: 50%;
    background: var(--royal-blue);
    display: flex; align-items: center; justify-content: center;
    flex: none;
  }
  .contacts__icon svg { width: 14px; height: 14px; }
  .contacts__icon--social { background: #c8367a; }

  .band-blue {
    position: absolute; left: 0; bottom: 0;
    width: 530px; height: 18px; background: var(--royal-blue);
  }
  .band-black {
    position: absolute; right: 0; bottom: 0;
    width: 262px; height: 54px; background: var(--card-black);
  }
</style>
</head>
<body>
<main class="sheet">
  <section class="card card--front" aria-label="Card front">
    <div class="brand">
      <span class="brand__dot"></span>
      <span class="brand__name" style="color:var(--card-white)">T. Lane Studio</span>
    </div>
  </section>

  <section class="card card--back" aria-label="Card back">
    <div class="brand">
      <span class="brand__dot"></span>
      <span class="brand__name">T. Lane Studio</span>
    </div>

    <div class="divider"></div>

    <ul class="contacts">
      <li class="contacts__item">
        <span class="contacts__icon">
          <svg viewBox="0 0 24 24" fill="#fff"><path d="M6.6 10.8a15 15 0 0 0 6.6 6.6l2.2-2.2a1 1 0 0 1 1-.25 11.4 11.4 0 0 0 3.6.57 1 1 0 0 1 1 1V20a1 1 0 0 1-1 1A17 17 0 0 1 3 4a1 1 0 0 1 1-1h3.5a1 1 0 0 1 1 1c0 1.25.2 2.45.57 3.6a1 1 0 0 1-.25 1z"/></svg>
        </span>
        916-384-7702
      </li>
      <li class="contacts__item">
        <span class="contacts__icon">
          <svg viewBox="0 0 24 24" fill="none" stroke="#fff" stroke-width="2"><rect x="3" y="6" width="18" height="12"/><path d="M3 6l9 7 9-7"/></svg>
        </span>
        info@tlane-studio.example
      </li>
      <li class="contacts__item">
        <span class="contacts__icon">
          <svg viewBox="0 0 24 24" fill="none" stroke="#fff" stroke-width="2"><circle cx="12" cy="12" r="9"/><path d="M3 12h18M12 3c3 3 3 15 0 18M12 3c-3 3-3 15 0 18"/></svg>
        </span>
        www.tlane-studio.example
      </li>
      <li class="contacts__item">
        <span class="contacts__icon contacts__icon--social"></span>
        @t.lanestudio
      </li>
    </ul>

    <div class="band-blue"></div>
    <div class="band-black"></div>
  </section>
</main>
</body>
</html>
```